Harborline Lending and Capital. We provide MOSTLY residential home mortgages in Florida AND commercial loans for investment properties throughout the United states.
I would love to emulate so of the lender sites that are available on the internet but I would like to have the site as popular as possible for SEO purposes. Clients can already click the link to take them to the mortgage application where they can complete that and upload documents. If you could polish that up for me that would be great. I can also provide you with great detail on loan programs that are currently being offered. WE OFFER ALL MORTGAGE LENDING PRODUCTS. I would also like to add something in reference to the rate but I don't think it's legal to actually state or promise a rate for mortgage since they vary based on loan type, client and other criteria...

On the Harborline real estate site I would like to add a link or some way for clients to be able to put in credit card information to render services ...

Please let me know what you need from me

Thank you !!

Current link to site to improve and code

https://harborlinelendingandcapital.example/

Industry/Entity Type

Residential and commmercial lending

Coding

Coded - Design and coding required

Number of Pages Required

2 page

Requirements
Must have
• Love to integrate Mortgage interest rates even if general
Nice to have
• Link to fill out mortgage application via Quorvel LPX software

```html
<!DOCTYPE html>
<html lang="en">
<head>
<meta charset="utf-8">
<title>Harborline Lending and Capital</title>
<link href="https://fonts.googleapis.com/css2?family=Poppins:wght@300;400;500;600;700;800&family=Marcellus&display=swap" rel="stylesheet">
<style>
:root{
  --green-dark:#1d3b24;
  --green-deep:#173020;
  --lime:#93bf3c;
  --lime-soft:#eef3dc;
  --cream:#f6f7ee;
  --ink:#1c1c1c;
  --muted:#555;
  --line:#dcdcdc;
  --chart:#ef8a4c;
  --white:#fff;
}
*{box-sizing:border-box;margin:0;padding:0}
html,body{width:1200px;height:4835px;overflow:hidden}
body{font-family:"Poppins",sans-serif;color:var(--ink);background:var(--white);position:relative}
section,header,footer{position:absolute;left:0;width:1200px}
.abs{position:absolute}
.btn-lime{position:absolute;background:var(--lime);color:var(--green-dark);border-radius:40px;font-size:12px;font-weight:500;display:flex;align-items:center;justify-content:center;gap:8px}
.btn-outline{position:absolute;border:1.5px solid var(--green-dark);border-radius:40px;font-size:12px;font-weight:500;display:flex;align-items:center;justify-content:center;gap:8px;color:var(--green-dark)}
.section-title{position:absolute;left:0;width:1200px;text-align:center;font-size:34px;font-weight:300;letter-spacing:.5px;text-transform:uppercase;color:var(--ink)}
.section-title b{font-weight:700;color:var(--green-dark)}
.underline{position:absolute;left:556px;width:88px;height:4px;background:var(--lime);border-radius:2px}

/* header */
.site-header{top:0;height:100px;background:var(--white)}
.brand{position:absolute;left:140px;top:26px;display:flex;align-items:center;gap:12px}
.brand-mark{width:40px;height:40px;border-radius:50%;background:var(--green-dark)}
.brand-name{font-size:13px;font-weight:700;color:var(--green-dark);line-height:1.2;width:220px}
.nav{position:absolute;left:700px;top:38px;display:flex;gap:30px;font-size:13px;color:var(--ink)}
.nav-cta{position:absolute;left:952px;top:33px;width:106px;height:34px;background:var(--lime);color:var(--white);font-size:13px;border-radius:4px;display:flex;align-items:center;justify-content:center}

/* hero */
.hero{top:100px;height:530px;background:linear-gradient(100deg,#fbfbf4 0%,#fdf8ec 45%,#fde9e4 78%,#fbf4ec 100%)}
.hero h1{position:absolute;left:142px;top:140px;font-size:33px;line-height:39px;font-weight:800;text-transform:uppercase;color:var(--green-dark)}
.hero h1 span{color:var(--lime);text-decoration:underline;text-decoration-thickness:3px;text-underline-offset:4px}
.hero p{position:absolute;left:142px;top:268px;width:380px;font-size:15px;line-height:22px;color:#333}
.hero .btn-dark{position:absolute;left:142px;top:328px;width:143px;height:42px;background:var(--green-dark);color:var(--white);font-size:12px;border-radius:4px;display:flex;align-items:center;justify-content:center}
.hero-photo{position:absolute;left:663px;top:52px;width:395px;height:436px;border-radius:22px;background:linear-gradient(160deg,#cfd6da 0%,#a9b1a8 45%,#6b5a45 80%,#4e3d30 100%)}
.dots{position:absolute;left:615px;top:70px}
.hero-badge{position:absolute;width:52px;height:52px;border-radius:50%;background:var(--white);box-shadow:0 4px 14px rgba(0,0,0,.12)}

/* stats */
.stats{top:630px;height:115px;background:var(--lime-soft);display:flex}
.stat{position:absolute;width:220px;text-align:center;top:28px}
.stat strong{display:block;font-family:"Marcellus",serif;font-size:29px;font-weight:400;color:#222}
.stat span{display:block;font-size:12px;margin-top:8px;text-transform:uppercase;color:#222}

/* properties */
.properties{top:745px;height:600px}
.prop-card{position:absolute;top:143px;width:210px;height:295px;border:1px solid #e2e2e2;border-radius:10px;background:var(--white);box-shadow:0 2px 8px rgba(0,0,0,.05)}
.prop-img{position:absolute;left:8px;top:8px;width:194px;height:224px;border-radius:4px}
.prop-count{position:absolute;top:245px;width:100%;text-align:center;font-size:11px;color:var(--lime)}
.prop-name{position:absolute;top:262px;width:100%;text-align:center;font-size:14px;font-weight:500}
.arrow-btn{position:absolute;top:272px;width:36px;height:36px;border-radius:50%;display:flex;align-items:center;justify-content:center}

/* about */
.about{top:1345px;height:500px}
.about-photo{position:absolute;left:127px;top:0;width:403px;height:418px;border-radius:60px 0 0 0;background:linear-gradient(180deg,#7fa6c9 0%,#b9c3c4 40%,#cfc4b0 65%,#4a5b43 100%)}
.years{position:absolute;left:440px;top:92px;width:150px;height:150px;border-radius:50%;background:var(--lime);color:var(--white);display:flex;flex-direction:column;align-items:center;justify-content:center}
.years strong{font-size:52px;font-weight:600;line-height:1}
.years span{font-size:10px;font-weight:500;margin-top:6px}
.about-eyebrow{position:absolute;left:640px;top:0;font-family:"Marcellus",serif;font-size:18px;color:var(--lime);letter-spacing:.5px}
.about h2{position:absolute;left:640px;top:30px;font-size:34px;line-height:44px;font-weight:300;text-transform:uppercase}
.about h2 b{font-weight:700;color:var(--green-dark)}
.about-text{position:absolute;left:640px;top:140px;width:420px;font-size:12.5px;line-height:25.5px;color:#333}
.call{position:absolute;left:790px;top:362px;display:flex;align-items:center;gap:10px}
.call-icon{width:42px;height:42px;border-radius:50%;background:var(--green-dark);display:flex;align-items:center;justify-content:center}
.call small{display:block;font-size:8px;font-weight:600}
.call strong{font-size:11.5px;font-weight:600;color:var(--green-dark)}

/* services */
.services{top:1845px;height:560px}
.services-bg{position:absolute;left:0;top:0;width:1200px;height:413px;background:linear-gradient(180deg,#7ea9d3 0%,#a7c3dc 45%,#6e8fa3 72%,#2e5f7d 100%)}
.services .section-title{top:158px;color:var(--white)}
.services .section-title b{color:var(--white)}
.service-card{position:absolute;top:285px;width:288px;height:260px;background:var(--white);border-radius:10px;box-shadow:0 6px 20px rgba(0,0,0,.08);text-align:center}
.service-icon{position:absolute;left:102px;top:-45px;width:84px;height:84px;border-radius:12px;background:var(--lime);display:flex;align-items:center;justify-content:center;box-shadow:0 0 0 8px rgba(255,255,255,.5)}
.service-card h3{position:absolute;top:68px;width:100%;font-size:19px;font-weight:600;text-transform:uppercase;color:var(--green-dark)}
.service-card p{position:absolute;top:100px;left:24px;width:240px;font-size:12.5px;line-height:25px;color:#333}
.service-card .btn-outline{left:77px;top:190px;width:134px;height:40px}

/* rates */
.rates{top:2405px;height:870px}
.rates h2{position:absolute;top:62px;width:1200px;text-align:center;font-size:34px;line-height:46px;font-weight:300;text-transform:uppercase}
.rates h2 b{font-weight:700;color:var(--green-dark)}
.rates-text{position:absolute;left:300px;top:190px;width:600px;text-align:center;font-size:12.5px;line-height:25px;color:#333}
.chart-card{position:absolute;left:330px;top:295px;width:540px;height:412px;background:var(--white);border-radius:10px;box-shadow:0 2px 14px rgba(0,0,0,.1)}
.chart-card h4{position:absolute;left:8px;top:12px;font-size:16.5px;font-weight:700}
.chart-card p{position:absolute;left:8px;top:40px;width:500px;font-size:10px;line-height:14px;color:#333}
.chart-card svg{position:absolute;left:0;top:78px}

/* testimonials */
.testimonials{top:3275px;height:590px;background:var(--cream)}
.testimonials .section-title{top:88px}
.quote-card{position:absolute;top:167px;width:435px;height:270px;background:var(--white);border-radius:10px;box-shadow:0 2px 14px rgba(0,0,0,.05)}
.avatar{position:absolute;left:26px;top:26px;width:62px;height:62px;border-radius:8px}
.q-name{position:absolute;left:100px;top:34px;font-size:15px;font-weight:600}
.stars{position:absolute;left:100px;top:58px;color:#8fbd36;font-size:13px;letter-spacing:2px}
.q-mark{position:absolute;right:20px;top:36px;font-family:"Poppins",sans-serif;font-size:72px;font-weight:800;line-height:.6;color:var(--lime)}
.q-text{position:absolute;left:26px;top:118px;width:390px;font-size:12.5px;line-height:25px;color:#333}
.pager{position:absolute;top:485px;left:535px;display:flex;gap:18px;align-items:center}
.pager i{width:6px;height:6px;border-radius:50%;background:#aaa;display:block}
.pager i.on{width:14px;height:14px;border:2px solid var(--lime);background:radial-gradient(circle,var(--lime) 3px,transparent 4px)}

/* contact */
.contact{top:3865px;height:595px}
.contact .section-title{top:82px}
.contact-sub{position:absolute;top:142px;width:1200px;text-align:center;font-size:12.5px;color:#333}
.field{position:absolute;height:52px;border:1px solid var(--line);border-radius:4px;display:flex;align-items:center;font-size:11px;color:#888;padding-left:14px;gap:10px;background:var(--white)}
.field .sep{width:1px;height:20px;background:var(--line)}
.send{position:absolute;left:292px;top:460px;width:616px;height:52px;background:var(--lime);color:var(--green-dark);border-radius:4px;font-size:13px;font-weight:500;display:flex;align-items:center;justify-content:center;text-transform:uppercase}

/* footer */
.site-footer{top:4460px;height:375px;background:var(--green-deep);color:var(--white)}
.f-brand{position:absolute;left:140px;top:72px;display:flex;align-items:center;gap:10px}
.f-brand .brand-mark{background:var(--white);width:34px;height:34px}
.f-brand .brand-name{color:var(--white);font-size:12px}
.f-note{position:absolute;left:140px;top:140px;width:290px;font-size:12.5px;line-height:21px}
.f-input{position:absolute;left:140px;top:196px;width:262px;height:34px;border-radius:30px;background:var(--white);color:#999;font-size:11px;display:flex;align-items:center;padding-left:30px}
.f-input i{position:absolute;right:4px;top:4px;width:26px;height:26px;border-radius:50%;background:var(--lime);display:flex;align-items:center;justify-content:center}
.f-col h5{font-size:17px;font-weight:500;margin-bottom:10px}
.f-col{position:absolute;top:72px;font-size:12.5px;line-height:28px}
.f-row{display:flex;gap:10px;line-height:20px;margin-bottom:10px}
.social{display:flex;align-items:center;gap:12px;line-height:30px;margin-bottom:10px}
.social i{width:30px;height:30px;border-radius:50%;border:1.5px solid var(--white);display:block}
.social i.on{background:var(--lime);border-color:var(--lime)}
.copyright{position:absolute;bottom:16px;width:1200px;text-align:center;font-size:12px}
</style>
</head>
<body>

<header class="site-header">
  <div class="brand"><div class="brand-mark"></div><div class="brand-name">HARBORLINE LENDING AND CAPITAL</div></div>
  <nav class="nav"><span>Home</span><span>About Us</span><span>Properties</span></nav>
  <div class="nav-cta">Contact Us</div>
</header>

<section class="hero">
  <h1>Unlock your future<br>with our tailored<br>mortgage <span>solutions</span></h1>
  <p>Residential and Commercial Mortgages across Florida and the USA</p>
  <div class="btn-dark">Get Started Now</div>
  <svg class="dots" width="60" height="140" aria-hidden="true">
    <g fill="#333">
      <circle cx="3" cy="3" r="1.6"/><circle cx="18" cy="3" r="1.6"/><circle cx="33" cy="3" r="1.6"/><circle cx="48" cy="3" r="1.6"/>
      <circle cx="3" cy="23" r="1.6"/><circle cx="18" cy="23" r="1.6"/><circle cx="33" cy="23" r="1.6"/><circle cx="48" cy="23" r="1.6"/>
      <circle cx="3" cy="43" r="1.6"/><circle cx="18" cy="43" r="1.6"/><circle cx="33" cy="43" r="1.6"/><circle cx="48" cy="43" r="1.6"/>
      <circle cx="3" cy="63" r="1.6"/><circle cx="18" cy="63" r="1.6"/><circle cx="33" cy="63" r="1.6"/><circle cx="48" cy="63" r="1.6"/>
      <circle cx="3" cy="83" r="1.6"/><circle cx="18" cy="83" r="1.6"/><circle cx="33" cy="83" r="1.6"/><circle cx="48" cy="83" r="1.6"/>
      <circle cx="3" cy="103" r="1.6"/><circle cx="18" cy="103" r="1.6"/><circle cx="33" cy="103" r="1.6"/><circle cx="48" cy="103" r="1.6"/>
      <circle cx="3" cy="123" r="1.6"/><circle cx="18" cy="123" r="1.6"/>
    </g>
  </svg>
  <div class="hero-photo" role="img" aria-label="Smiling couple standing in front of a white house with a gabled porch"></div>
  <div class="hero-badge" style="left:1032px;top:92px" role="img" aria-label="Money bag icon badge"></div>
  <div class="hero-badge" style="left:643px;top:342px" role="img" aria-label="House icon badge"></div>
</section>

<section class="stats">
  <div class="stat" style="left:115px"><strong>850+</strong><span>Elegant Apartments</span></div>
  <div class="stat" style="left:378px"><strong>950+</strong><span>Luxury Houses</span></div>
  <div class="stat" style="left:625px"><strong>18k+</strong><span>Satisfied Guests</span></div>
  <div class="stat" style="left:870px"><strong>850+</strong><span>Happy Owners</span></div>
</section>

<section class="properties">
  <h2 class="section-title" style="top:68px">Available <b>Properties</b></h2>
  <div class="underline" style="top:115px"></div>
  <div class="arrow-btn" style="left:69px;border:1.5px solid #333">
    <svg width="14" height="12" viewBox="0 0 14 12"><path d="M13 6H2M6 1 1 6l5 5" fill="none" stroke="#333" stroke-width="1.5"/></svg>
  </div>
  <div class="prop-card" style="left:142px"><div class="prop-img" role="img" aria-label="Modern white apartment facade with dark windows" style="background:linear-gradient(180deg,#bcd4e8,#e6e6e2 40%,#9a9c9c)"></div><div class="prop-count">12 PROPERTY</div><div class="prop-name">Sunset Street</div></div>
  <div class="prop-card" style="left:375px"><div class="prop-img" role="img" aria-label="Dark modern house lit at dusk" style="background:linear-gradient(180deg,#2f4f78,#35414f 55%,#b57a3a)"></div><div class="prop-count">34 PROPERTY</div><div class="prop-name">Union Avenue</div></div>
  <div class="prop-card" style="left:608px"><div class="prop-img" role="img" aria-label="Contemporary house with wood panels and patio" style="background:linear-gradient(180deg,#6e9fd6,#cfd2cf 55%,#a98456)"></div><div class="prop-count">56 PROPERTY</div><div class="prop-name">Washington Street</div></div>
  <div class="prop-card" style="left:840px"><div class="prop-img" role="img" aria-label="Brick and glass residential building" style="background:linear-gradient(180deg,#7ea8d8,#8e5a45 50%,#4b5a66)"></div><div class="prop-count">78 PROPERTY</div><div class="prop-name">Oak Boulevard</div></div>
  <div class="arrow-btn" style="left:1095px;background:var(--lime)">
    <svg width="14" height="12" viewBox="0 0 14 12"><path d="M1 6h11M8 1l5 5-5 5" fill="none" stroke="#fff" stroke-width="1.5"/></svg>
  </div>
  <div class="btn-lime" style="left:533px;top:470px;width:134px;height:40px">VIEW MORE <svg width="14" height="10"><path d="M0 5h12M8 1l4 4-4 4" fill="none" stroke="#1d3b24" stroke-width="1.3"/></svg></div>
</section>

<section class="about">
  <div class="about-photo" role="img" aria-label="Luxury modern villa with garden at twilight"></div>
  <div class="years"><strong>25+</strong><span>YEARS OF EXPERIENCE</span></div>
  <div class="about-eyebrow">ABOUT</div>
  <h2>Harborline <b>Lending<br>and Capital</b></h2>
  <p class="about-text">Harborline Lending Originates Residential Home loans in Florida and Commercial and business financing in all 50 States. We have over 25 years of experience in ALL types of real estate and commercial lending. We are strategically partnered to help you obtain ALL necessary components of residential and commercial lending. From the RIGHT lending partners to the best practice Insurance avenues and commercial and residential real estate partners</p>
  <div class="btn-lime" style="left:640px;top:363px;width:134px;height:40px">READ MORE <svg width="14" height="10"><path d="M0 5h12M8 1l4 4-4 4" fill="none" stroke="#1d3b24" stroke-width="1.3"/></svg></div>
  <div class="call">
    <div class="call-icon"><svg width="18" height="18" viewBox="0 0 24 24"><path d="M6.6 10.8a15 15 0 0 0 6.6 6.6l2.2-2.2c.3-.3.7-.4 1-.2 1.1.4 2.3.6 3.6.6.6 0 1 .4 1 1V20c0 .6-.4 1-1 1A17 17 0 0 1 3 4c0-.6.4-1 1-1h3.5c.6 0 1 .4 1 1 0 1.3.2 2.5.6 3.6.1.3 0 .7-.2 1z" fill="#93bf3c"/></svg></div>
    <div><small>CALL US</small><strong>+0 (555) 014-2290</strong></div>
  </div>
</section>

<section class="services">
  <div class="services-bg" role="img" aria-label="City skyline on the waterfront with a Ferris wheel under blue sky"></div>
  <h2 class="section-title">Our <b>Services</b></h2>
  <div class="service-card" style="left:142px">
    <div class="service-icon"><svg width="44" height="44" viewBox="0 0 44 44" fill="none" stroke="#fff" stroke-width="2.2"><rect x="8" y="14" width="28" height="26"/><path d="M4 14h36M14 6h16v8M14 22h4M26 22h4M14 30h4M26 30h4M19 40v-6h6v6"/></svg></div>
    <h3>Commercial Loans</h3>
    <p>Lorem Ipsum is simply dummy text of the printing and typesetting industry. Lorem Ipsum has been</p>
    <div class="btn-outline">READ MORE <svg width="14" height="10"><path d="M0 5h12M8 1l4 4-4 4" fill="none" stroke="#1d3b24" stroke-width="1.3"/></svg></div>
  </div>
  <div class="service-card" style="left:456px">
    <div class="service-icon"><svg width="44" height="44" viewBox="0 0 44 44" fill="none" stroke="#fff" stroke-width="2.4"><path d="M4 22 22 6l18 16M9 18v20h26V18"/><rect x="17" y="24" width="10" height="8"/></svg></div>
    <h3>Residential Loans</h3>
    <p>Lorem Ipsum is simply dummy text of the printing and typesetting industry. Lorem Ipsum has been</p>
    <div class="btn-outline">READ MORE <svg width="14" height="10"><path d="M0 5h12M8 1l4 4-4 4" fill="none" stroke="#1d3b24" stroke-width="1.3"/></svg></div>
  </div>
  <div class="service-card" style="left:770px">
    <div class="service-icon"><svg width="44" height="44" viewBox="0 0 44 44" fill="none" stroke="#fff" stroke-width="2.4"><path d="M4 20 18 8l10 8M8 17v20h10"/><path d="M34 12 22 38"/><path d="M36 22c-2-3-8-2-8 1s8 2 8 6-7 4-9 1M31 18v3M31 33v3"/></svg></div>
    <h3>Property Mortgage</h3>
    <p>Lorem Ipsum is simply dummy text of the printing and typesetting industry. Lorem Ipsum has been</p>
    <div class="btn-outline">READ MORE <svg width="14" height="10"><path d="M0 5h12M8 1l4 4-4 4" fill="none" stroke="#1d3b24" stroke-width="1.3"/></svg></div>
  </div>
</section>

<section class="rates">
  <h2>Stay informed<br><b>about mortgage rates</b></h2>
  <p class="rates-text">Mortgage rates fluctuate based on various factors such as loan type, market conditions, and your personal financial profile. Rates may change frequently, and it's important to get the most accurate and up-to-date information for your unique situation.</p>
  <div class="chart-card">
    <h4>Last 90 Days of 30-Year Mortgage Rate Average</h4>
    <p>Average of nationwide rates for 30-year fixed-rate new purchase loans with at least a 20% down payment and an applicant credit score of 680 to 739.</p>
    <svg width="540" height="330" viewBox="0 0 540 330" font-family="Poppins, sans-serif" font-size="9">
      <g stroke="#e3e3e3" stroke-width="1">
        <line x1="40" y1="20" x2="520" y2="20"/><line x1="40" y1="51" x2="520" y2="51"/><line x1="40" y1="82" x2="520" y2="82"/><line x1="40" y1="113" x2="520" y2="113"/><line x1="40" y1="144" x2="520" y2="144"/><line x1="40" y1="175" x2="520" y2="175"/><line x1="40" y1="207" x2="520" y2="207"/><line x1="40" y1="238" x2="520" y2="238"/><line x1="40" y1="269" x2="520" y2="269"/><line x1="40" y1="300" x2="520" y2="300"/>
        <line x1="70" y1="20" x2="70" y2="300"/><line x1="110" y1="20" x2="110" y2="300"/><line x1="150" y1="20" x2="150" y2="300"/><line x1="190" y1="20" x2="190" y2="300"/><line x1="230" y1="20" x2="230" y2="300"/><line x1="270" y1="20" x2="270" y2="300"/><line x1="310" y1="20" x2="310" y2="300"/><line x1="350" y1="20" x2="350" y2="300"/><line x1="390" y1="20" x2="390" y2="300"/><line x1="430" y1="20" x2="430" y2="300"/><line x1="470" y1="20" x2="470" y2="300"/><line x1="510" y1="20" x2="510" y2="300"/>
      </g>
      <g fill="#333" text-anchor="end">
        <text x="30" y="23">7.8%</text><text x="30" y="54">7.6</text><text x="30" y="85">7.4</text><text x="30" y="116">7.2</text><text x="30" y="147">7.0</text><text x="30" y="178">6.8</text><text x="30" y="210">6.6</text><text x="30" y="241">6.4</text><text x="30" y="272">6.2</text><text x="30" y="303">6.0</text>
      </g>
      <g fill="#333" text-anchor="middle">
        <text x="70" y="318">2/19</text><text x="110" y="318">2/26</text><text x="150" y="318">3/4</text><text x="190" y="318">3/11</text><text x="230" y="318">3/18</text><text x="270" y="318">3/25</text><text x="310" y="318">4/1</text><text x="350" y="318">4/8</text><text x="390" y="318">4/15</text><text x="430" y="318">4/22</text><text x="470" y="318">4/29</text><text x="510" y="318">5/6</text>
      </g>
      <polyline fill="none" stroke="#ef8a4c" stroke-width="2" points="45,147.5 57.5,141.3 70,136.6 82.5,149.1 95,144.4 107.5,155.3 120,163.1 132.5,175.5 145,188 157.5,202 170,194.2 182.5,183.3 195,163.1 207.5,152.2 220,167.7 232.5,184.9 245,191.1 257.5,197.3 270,188 282.5,175.5 295,160 307.5,147.5 320,152.2 332.5,128.8 345,121.1 357.5,110.2 370,116.4 382.5,100.8 395,110.2 407.5,97.7 420,86.8 432.5,100.8 445,121.1 457.5,128.8 470,125.7 482.5,136.6 495,131.9"/>
      <g fill="#fff" stroke="#555" stroke-width="1.5">
        <circle cx="70" cy="136.6" r="3.5"/><circle cx="157.5" cy="202" r="3.5"/><circle cx="207.5" cy="152.2" r="3.5"/><circle cx="257.5" cy="197.3" r="3.5"/><circle cx="420" cy="86.8" r="3.5"/><circle cx="482.5" cy="136.6" r="3.5"/>
      </g>
      <g fill="#1f3c8a" font-weight="600" text-anchor="middle">
        <text x="70" y="112">7.05%</text><text x="70" y="123">Feb 22</text>
        <text x="157.5" y="217">6.63%</text><text x="157.5" y="228">Mar 8–10</text>
        <text x="207.5" y="125">6.95%</text><text x="207.5" y="136">Mar 16–17</text>
        <text x="257.5" y="213">6.66%</text><text x="257.5" y="224">Mar 27</text>
        <text x="420" y="62">7.37%</text><text x="420" y="73">Apr 25</text>
        <text x="482.5" y="155">7.05%</text><text x="482.5" y="166">May 13</text>
      </g>
    </svg>
  </div>
  <div class="btn-lime" style="left:540px;top:745px;width:120px;height:40px">SIGN UP <svg width="14" height="10"><path d="M0 5h12M8 1l4 4-4 4" fill="none" stroke="#1d3b24" stroke-width="1.3"/></svg></div>
</section>

<section class="testimonials">
  <h2 class="section-title">What our <b>clients say</b></h2>
  <div class="quote-card" style="left:-330px">
    <div class="q-mark">&rdquo;</div>
    <p class="q-text">Lorem Ipsum Is Simply Dummy Text Of The Printintypesetting Industry. Lorem Ipsum Has Been The Industry's Standdummy Text Ever Since The 1500s, When An Unknown Printer Togalley Of Type And Scrambled It To Make A Type Specimen Book. It</p>
  </div>
  <div class="quote-card" style="left:142px">
    <div class="avatar" role="img" aria-label="Client portrait" style="background:linear-gradient(160deg,#d9d9d9,#7a7a7a)"></div>
    <div class="q-name">Dorian Vale</div><div class="stars">★★★★★</div>
    <div class="q-mark">&rdquo;</div>
    <p class="q-text">Lorem Ipsum Is Simply Dummy Text Of The Printintypesetting Industry. Lorem Ipsum Has Been The Industry's Standdummy Text Ever Since The 1500s, When An Unknown Printer Togalley Of Type And Scrambled It To Make A Type Specimen Book. It Has Survived Not Only Five Centuries</p>
  </div>
  <div class="quote-card" style="left:624px">
    <div class="avatar" role="img" aria-label="Client portrait" style="background:linear-gradient(160deg,#e2c6b4,#6d4a3c)"></div>
    <div class="q-name">Mirela Kost</div><div class="stars">★★★★★</div>
    <div class="q-mark">&rdquo;</div>
    <p class="q-text">Lorem Ipsum Is Simply Dummy Text Of The Printintypesetting Industry. Lorem Ipsum Has Been The Industry's Standdummy Text Ever Since The 1500s, When An Unknown Printer Togalley Of Type And Scrambled It To Make A Type Specimen Book. It Has Survived Not Only Five Centuries</p>
  </div>
  <div class="quote-card" style="left:1118px">
    <div class="avatar" role="img" aria-label="Client portrait" style="background:linear-gradient(160deg,#cfe0c4,#7d8c6a)"></div>
    <p class="q-text">Lorem Ipsum Is Simply Dummy Text Of The Printintypesetting Industry. Lorem Ipsum Has Been The Industry's Standdummy Text Ever Since The 1500s, When An Unknown Printer Togalley Of Type And Scrambled It To Make A Type Specimen Book. It Has Survived</p>
  </div>
  <div class="pager"><i></i><i></i><i class="on"></i><i></i><i></i><i></i></div>
</section>

<section class="contact">
  <h2 class="section-title">Get in <b>touch</b></h2>
  <p class="contact-sub">Please Send Me A Message For General Inquiries Or Reservations.</p>
  <div class="field" style="left:292px;top:202px;width:300px">
    <svg width="14" height="14" viewBox="0 0 14 14" fill="none" stroke="#aaa"><circle cx="7" cy="4.5" r="3"/><path d="M1.5 13c0-3 2.5-5 5.5-5s5.5 2 5.5 5"/></svg><span class="sep"></span>First Name</div>
  <div class="field" style="left:608px;top:202px;width:300px">
    <svg width="14" height="14" viewBox="0 0 14 14" fill="none" stroke="#aaa"><circle cx="7" cy="4.5" r="3"/><path d="M1.5 13c0-3 2.5-5 5.5-5s5.5 2 5.5 5"/></svg><span class="sep"></span>Last Name</div>
  <div class="field" style="left:292px;top:270px;width:300px">
    <svg width="14" height="12" viewBox="0 0 14 12" fill="none" stroke="#aaa"><rect x="1" y="1" width="12" height="10"/><path d="M1 1l6 5 6-5"/></svg><span class="sep"></span>Your Email</div>
  <div class="field" style="left:608px;top:270px;width:300px">
    <svg width="14" height="14" viewBox="0 0 24 24" fill="none" stroke="#aaa" stroke-width="2"><path d="M6.6 10.8a15 15 0 0 0 6.6 6.6l2.2-2.2c.3-.3.7-.4 1-.2 1.1.4 2.3.6 3.6.6.6 0 1 .4 1 1V20c0 .6-.4 1-1 1A17 17 0 0 1 3 4c0-.6.4-1 1-1h3.5c.6 0 1 .4 1 1 0 1.3.2 2.5.6 3.6.1.3 0 .7-.2 1z"/></svg><span class="sep"></span>Phone</div>
  <div class="field" style="left:292px;top:338px;width:616px;height:108px;align-items:flex-start;padding-top:18px">
    <svg width="14" height="14" viewBox="0 0 14 14" fill="none" stroke="#aaa"><path d="M1 2h12v8H5l-3 3V2z"/></svg><span class="sep"></span>Your Message</div>
  <div class="send">Send Message</div>
</section>

<footer class="site-footer">
  <div class="f-brand"><div class="brand-mark"></div><div class="brand-name">HARBORLINE LENDING AND CAPITAL</div></div>
  <p class="f-note">Latest Updates, Exclusive Content, And Special Offers? Subscribe To Our Newsletter!</p>
  <div class="f-input">Your Email<i><svg width="12" height="10"><path d="M0 5h10M6 1l4 4-4 4" fill="none" stroke="#173020" stroke-width="1.4"/></svg></i></div>
  <div class="f-col" style="left:481px"><h5>Quick Links</h5><div>Home</div><div>About Us</div><div>Properties</div><div>Contact Us</div></div>
  <div class="f-col" style="left:634px;width:260px">
    <h5>Contact Details</h5>
    <div class="f-row"><svg width="14" height="16" viewBox="0 0 14 18"><path d="M7 0a7 7 0 0 0-7 7c0 5 7 11 7 11s7-6 7-11a7 7 0 0 0-7-7zm0 10a3 3 0 1 1 0-6 3 3 0 0 1 0 6z" fill="#fff"/></svg><span>418 Cypress Landing Way,<br>Bayview, FL USA</span></div>
    <div class="f-row"><svg width="14" height="14" viewBox="0 0 24 24"><path d="M6.6 10.8a15 15 0 0 0 6.6 6.6l2.2-2.2c.3-.3.7-.4 1-.2 1.1.4 2.3.6 3.6.6.6 0 1 .4 1 1V20c0 .6-.4 1-1 1A17 17 0 0 1 3 4c0-.6.4-1 1-1h3.5c.6 0 1 .4 1 1 0 1.3.2 2.5.6 3.6.1.3 0 .7-.2 1z" fill="#fff"/></svg><span>Phone<br>+1 555 017 3346</span></div>
    <div class="f-row"><svg width="14" height="12" viewBox="0 0 14 12"><rect x="0" y="1" width="14" height="10" fill="#fff"/><path d="M0 1l7 5 7-5" fill="none" stroke="#173020"/></svg><span>Email<br><span style="font-size:10.5px">info@harborlinelendingandcapital.example</span></span></div>
  </div>
  <div class="f-col" style="left:940px">
    <h5>Social Media</h5>
    <div class="social"><i class="on"></i>Social Feed</div>
    <div class="social"><i></i>Video Channel</div>
    <div class="social"><i></i>Pro Network</div>
    <div class="social"><i></i>Photo Stream</div>
  </div>
  <div class="copyright">© 2025 Harborline Lending And Capital. All Rights Reserved.</div>
</footer>

</body>
</html>
```